Mobile Repair Service on location needs a Web Design

We are starting a new mobile device repair service called Handset Haven and our website needs a design!

Hello Designers!
First, we'd like to make clear this is more than a simple web design contest, we want the designers to create an idea. We want someone who can create the whole theme of the service's we provide. We want someone that can help design our visual branding, help us communicate a sentiment. And we are willing to pay for that.

Who are we?
Our company is based in Rotterdam, the Netherlands. We provide different services for all kinds of electronic devices. The kind of services we provide are, among other things, installations of hardware and software and the repair of broken or malfunctioning devices.
We are starting a new service that offers mobile device repairs on location, be it at the home of our customers, their office, or any other place. Just give us the address and we will come to you for the repair job. This is also our main USP. We have multiple skilled engineers who drive trough the country on a daily basis and can be on location within a working day. Repair is done immediately onsite while the customer waits. At this stage we will start with the smartphone product-group within the mobile devices. In a second phase we might also add tablets.
People don't want to be without their phone for weeks because of some parts that needed to be ordered by a repair center they had to sent their phone to. We offer a fully functional mobile repair center in the form of specially customized vans. These vans have all the tools and utilities needed by our engineers to safely repair your mobile device. Your phone is being repaired directly in front of you, the next business-day, on a location you desire.

For this new service we are creating a website called Handset Haven. The website needs a story and matching design and this is where you come in. We are not looking for a simple template design we can get from any place. We need a story. We want you to create an idea, build a unique theme or vision that helps sell the product/service. This goes beyond the design of the website. We need the whole package, the design you are creating needs to have returning elements like icons, color use, images, maybe even characters etc. You name it! There needs to be a common thread in the design so we can reuse elements in, for example, the email templates, the work order or receipt we give to our customers (we may contact the winner of the contest to design these for us as well!).

The name 'Handset Haven' is chosen. Rehab (short for rehabilitate) has a bold and playful tone to it and the design needs to reflect the name. So we're looking for a somewhat playful and cheeky design. Definitely not too serious and definitely modern. We already got a logo that we love and that fit's this description (see attached design documents for the logo). It's bold, powerful and fun. Our web design needs to reflect this as well and has to fit in with our logo.
We would really like it if the design somehow incorporates elements that highlight our unique selling points (repairs on location, we come to you etc.). We would really like some form of story telling in the design. Think clumsy people breaking their phones. Teenagers in tears because they have no access to their friends. People nowadays have the need to always be 'connected'. What happens when your phone is broken or malfunctioning? We're handling tech, we are nerds and a little bit weird, but we're professionals and here to help you with your problem. The sentiment Byte Brigade tries to communicate is something we really like. We're looking for fresh idea's, anything goes!

In an overview all Unique Selling Points of the Handset haven service:
- Professional service on location. Don’t ship to us we will come to you!
- Clear pricing upfront. No hidden cost.
- Next business-day repair.
- Backed by a professional call center open 12 hours a day and open on a Saturday as well
- Backed by a professional repair center with more then 12 years of experience
- Repair is done by certified engineers
- 1 year warranty on the repair

The process:
The main function of our website will be for customers to make a repair request. A customer will visit our website and can make a repair request immediately by going through a 'request-order-flow'. In this flow he or she will need to fill in some forms and can select wich type/model/brand of mobile device he or she has and what parts need to be repaired. After a request is placed we will call the customer back (within an hour) for a short intake and to set a date/time and location. Our engineer will meet the customer at the specified location and will repair the device onsite in one of our mobile repair centers, which is a specialized van equipped with all the tools needed for device restorations.
So in short the steps are:
- Choose your device and repair job
- Place the order
- Get a callback within the hour
- Set date and location
- We will come to you.

Website functionality:
Our website is our main form of communication. So the sentiment we want to communicate needs be reflected in the design. We need a main/front page designed (preferably a long scrolling page design) containing:
1. Customers will be able to request a repair job directly on our website. So there will need to be a prominent button/link at the top of our main page that will bring the customer to this 'request-order-flow'. This is the main flow which needs to be full focus on the front page. All other items are secondary.
2. The general information of who we are and what we do, and why the customer should choose us. Preferably in short bullet-point type keywords/sentences with icons or other visual cues. See our unique selling points to get an idea of the information that will be displayed here.
3. There needs to be a section that will explain the process (see above) of a repair request step-by- step, again in brief short key sentences and with (custom) icons.
4. There needs to be a section that explains to the customer he/she can always contact us if they are not sure what the problem is with their device, and for this reason are not sure what repair request they should order.
5. We want to implement some functionality that display customer ratings or customer reviews. So there needs to be room for some kind of widget of plugin we're going to implement which shows these reviews.
6. A 'For business section' where we will explain all the options we provide for corporate clients.
7. Social media links.
8. There needs to be a menu with buttons that leads to the all sections described in the previous points.

For now, we need a design for our front page. In the second phase, when we have picked our winner, we may ask the winner to design the page(s) for our request workflow as well.

EDIT:
Finally, we have a very specific order in mind for the different segments of our website. We would like you to add some more segments that were not in our original brief as well:

1. Top header with order/request button. (should instantly make clear our main USP, we do repairs on location)
2. Our process
3. Our unique selling points / why choose us
4. The kind of repairs we do (broken screens, broken batteries, water damage, broken camera's, no sound etc.)
5. A 'meet our team' section, where we introduce some of our engineers
6. A 'contact us for any questions' section/
7. Testimonials/user reviews
8. A section where we show key performance indicators
9. 'For businesses' sections
10.'Subscribe for newsletter' field
11. Social media buttons

Industry/Entity Type

It Service

Number of Pages Required

1 page

Font styles to use
Sans Serif

Requirements
Must have
• a main/front page, design only
• custom icons/images for banners, adverts online and in print (high res)
Nice to have
• Storytelling in our design.
• Design that fits with our brand new logo.
• Elements like icons to have a flat design.
• Keep in mind that the website will need to be responsive when designing! (Ideally provide an example of the mobile design as well)
• Create a fun and trustworthy feeling.

```html
<!DOCTYPE html>
<html lang="en">
<head>
<meta charset="utf-8">
<title>Handset Haven</title>
<link href="https://fonts.googleapis.com/css2?family=Raleway:wght@400;500;600;700;800&family=Open+Sans:wght@400;600&display=swap" rel="stylesheet">
<style>
:root{
  --orange:#e8561f;
  --orange-dark:#c8441a;
  --ink:#3a3a3a;
  --muted:#6b6b6b;
  --soft:#e6e8ea;
  --white:#ffffff;
  --line:#d6d6d6;
  --dark-btn:#3b3b3b;
}
*{box-sizing:border-box;margin:0;padding:0}
html,body{width:1200px;height:2177px;overflow:hidden;background:var(--white)}
body{font-family:'Open Sans',sans-serif;color:var(--ink);position:relative}
a{color:inherit;text-decoration:none}

/* header */
.site-header{position:relative;height:130px;border-bottom:3px solid var(--line);box-shadow:0 2px 4px rgba(0,0,0,.08)}
.brand{position:absolute;left:135px;top:22px;display:flex;align-items:center;gap:14px}
.brand-mark{width:72px;height:72px;border-radius:50%;background:var(--orange)}
.brand-name{font-family:'Raleway',sans-serif;font-weight:800;font-size:36px;line-height:34px;color:var(--ink);width:150px}
.utility{position:absolute;right:132px;top:40px;display:flex;gap:26px;font-size:12px;color:var(--ink)}
.utility span{display:flex;align-items:center;gap:8px}
.utility i{display:inline-block;width:9px;height:9px;background:var(--orange)}
.main-nav{position:absolute;right:92px;top:92px;display:flex;gap:0;font-family:'Raleway',sans-serif;font-size:13px;font-weight:500}
.main-nav a{padding:0 40px 0 0}
.main-nav a:last-child{padding-right:0;margin-right:40px}
.main-nav .active{color:var(--orange)}

/* hero */
.hero{position:relative;height:440px;background:linear-gradient(90deg,#e9ebed 0%,#dfe2e5 60%,#e6e8ea 100%);overflow:hidden}
.hero-photo{position:absolute;left:363px;top:0;width:837px;height:440px;background:radial-gradient(ellipse at 55% 55%,#55595e 0%,#8b9096 28%,#cfd3d7 55%,rgba(223,226,229,0) 75%)}
.hero-copy{position:absolute;left:131px;top:203px}
.hero-kicker{font-family:'Raleway',sans-serif;font-size:29px;font-weight:400;letter-spacing:1px;color:var(--ink)}
.hero-title{margin-top:22px;font-family:'Raleway',sans-serif;font-weight:800;font-size:49px;line-height:48px;color:var(--orange);letter-spacing:1px}
.btn{display:inline-flex;align-items:center;justify-content:center;background:linear-gradient(var(--orange),var(--orange-dark));color:var(--white);font-family:'Raleway',sans-serif;font-weight:700;border-radius:3px;box-shadow:0 2px 3px rgba(0,0,0,.2)}
.btn-quote{position:absolute;left:132px;top:259px;width:200px;height:46px;font-size:15px;letter-spacing:.5px}
.hero-dots{position:absolute;left:136px;top:345px;display:flex;gap:4px}
.hero-dots i{width:6px;height:6px;border-radius:50%;background:#9a9a9a}
.hero-dots i:first-child{background:var(--orange)}

/* section titles */
.section-title{font-family:'Raleway',sans-serif;font-weight:500;font-size:30px;color:var(--orange);letter-spacing:.5px}

/* steps */
.how{height:345px;text-align:center;padding-top:40px}
.steps{display:flex;justify-content:center;margin-top:44px;padding:0 100px}
.step{width:200px}
.step svg{height:100px;width:110px}
.step p{margin-top:16px;font-size:15px;line-height:24px;color:var(--muted)}

/* who */
.who{position:relative;height:469px;background:var(--soft);overflow:hidden}
.who-copy{position:absolute;left:131px;top:75px;width:470px}
.who-copy p{margin-top:18px;font-size:11px;line-height:19px;color:var(--muted)}
.who-copy .section-title{margin-bottom:8px}
.btn-more{margin-top:30px;width:104px;height:34px;font-size:12px}
.who-photo{position:absolute;left:631px;top:25px;width:450px;height:444px;border-radius:200px 200px 0 0;background:radial-gradient(ellipse at 50% 40%,#c79a7c 0%,#9a6a48 35%,#d9cfc5 65%,rgba(230,232,234,0) 80%)}

/* features */
.features{height:439px;text-align:center;padding-top:40px}
.feature-grid{display:grid;grid-template-columns:repeat(3,306px);justify-content:center;row-gap:38px;margin-top:42px}
.feature svg{height:44px;width:44px}
.feature p{margin-top:14px;font-size:15px;line-height:24px;color:var(--muted);padding:0 8px}

/* newsletter */
.newsletter{height:89px;background:var(--orange);display:flex;align-items:center;padding-left:132px}
.newsletter h3{font-family:'Raleway',sans-serif;font-weight:700;font-size:19px;color:var(--white);width:403px}
.newsletter .field{width:360px;height:35px;background:var(--white);border-radius:2px;font-size:13px;font-style:italic;color:var(--ink);padding:9px 12px}
.newsletter .btn-sign{margin-left:10px;width:161px;height:35px;background:linear-gradient(#4a4a4a,#2e2e2e);color:var(--white);font-family:'Raleway',sans-serif;font-weight:700;font-size:14px;border-radius:3px;display:flex;align-items:center;justify-content:center}

/* footer */
.site-footer{position:relative;height:280px}
.footer-col{position:absolute;top:28px}
.footer-col h4{font-family:'Raleway',sans-serif;font-weight:500;font-size:20px;color:var(--ink)}
.footer-col ul{list-style:none;margin-top:12px}
.footer-col li{font-size:10.5px;line-height:24px;color:var(--muted)}
.social{position:absolute;left:940px;top:40px;display:flex;gap:8px}
.social i{width:26px;height:26px;border-radius:50%;background:#8a8a8a}
.copyright{position:absolute;left:132px;top:241px;font-size:10px;color:var(--ink)}
</style>
</head>
<body>

<header class="site-header">
  <div class="brand">
    <span class="brand-mark"></span>
    <span class="brand-name">HANDSET HAVEN</span>
  </div>
  <div class="utility">
    <span><i></i>Account</span>
    <span><i></i>Lists</span>
    <span><i></i>Cart</span>
  </div>
  <nav class="main-nav">
    <a class="active">HOME</a>
    <a>ABOUT US</a>
    <a>SERVICES</a>
    <a>NEWS</a>
    <a>CONTACT US</a>
  </nav>
</header>

<section class="hero">
  <div class="hero-photo" role="img" aria-label="Hand tapping a smartphone beside a phone with a shattering screen"></div>
  <div class="hero-copy" style="top:0;left:0">
    <p class="hero-kicker" style="position:absolute;left:131px;top:76px;white-space:nowrap">WE PROVIDE</p>
    <h1 class="hero-title" style="position:absolute;left:131px;top:110px;white-space:nowrap">HARDWARE AND<br>SOFTWARE</h1>
    <a class="btn btn-quote">REQUEST A QUOTE</a>
    <div class="hero-dots" style="left:136px;top:345px"><i></i><i></i><i></i></div>
  </div>
</section>

<section class="how">
  <h2 class="section-title">HOW IT WORKS</h2>
  <div class="steps">
    <div class="step">
      <svg viewBox="0 0 110 100" fill="none" stroke="var(--orange)" stroke-width="2.5"><rect x="32" y="2" width="46" height="96" rx="6"/><line x1="32" y1="14" x2="78" y2="14"/><line x1="32" y1="84" x2="78" y2="84"/><line x1="50" y1="8" x2="60" y2="8"/></svg>
      <p>Choose your device and repair job</p>
    </div>
    <div class="step">
      <svg viewBox="0 0 110 100" fill="none" stroke="var(--ink)" stroke-width="2.5"><rect x="15" y="12" width="80" height="86" rx="6"/><path d="M40 12v-4h10a5 5 0 0 1 10 0h10v4l-4 6H44z"/><line x1="32" y1="46" x2="78" y2="46"/><line x1="32" y1="60" x2="78" y2="60"/><line x1="32" y1="74" x2="78" y2="74"/></svg>
      <p>Place the order</p>
    </div>
    <div class="step">
      <svg viewBox="0 0 110 100" fill="none" stroke="var(--ink)" stroke-width="2.5"><rect x="22" y="2" width="46" height="96" rx="6"/><line x1="22" y1="14" x2="68" y2="14"/><line x1="22" y1="84" x2="68" y2="84"/><path d="M45 44h30a12 12 0 0 1 0 24H60"/><path d="M52 36l-8 8 8 8"/></svg>
      <p>Get a callback within the hour</p>
    </div>
    <div class="step">
      <svg viewBox="0 0 110 100" fill="none" stroke="var(--ink)" stroke-width="2.5"><rect x="10" y="10" width="90" height="88" rx="4"/><line x1="10" y1="28" x2="100" y2="28"/><rect x="28" y="2" width="8" height="16" rx="2"/><rect x="74" y="2" width="8" height="16" rx="2"/><path d="M38 60l12 12 22-26"/></svg>
      <p>Set date and location</p>
    </div>
    <div class="step">
      <svg viewBox="0 0 110 100" fill="none" stroke="var(--ink)" stroke-width="2.5"><path d="M2 36l22-16 20 8 14-6 18 2 30 14-8 22-18 20"/><path d="M46 30l-12 14a6 6 0 0 0 10 6l14-10 24 22"/><path d="M28 58l6 6M36 52l10 10M44 60l10 10M52 68l8 8"/><path d="M2 36l10 26 20 20"/></svg>
      <p>We will come to you.</p>
    </div>
  </div>
</section>

<section class="who">
  <div class="who-copy">
    <h2 class="section-title">WHO ARE WE?</h2>
    <p>Our company is based in Rotterdam, the Netherlands. We provide different services for all kinds of electronic devices. The kind of services we provide are, among other things, installations of hardware and software and the repair of broken or malfunctioning devices.</p>
    <p>We are starting a new service that offers mobile device repairs on location, be it at the home of our customers, their office, or any other place. Just give us the address and we will come to you for the repair job. This is also our main USP. We have multiple skilled engineers who drive trough the country on a daily basis and can be on location within a working day. Repair is done immediately onsite while the customer waits.</p>
    <a class="btn btn-more">READ MORE</a>
  </div>
  <div class="who-photo" role="img" aria-label="Smiling customer holding up a repaired phone and giving a thumbs up"></div>
</section>

<section class="features">
  <h2 class="section-title">OUR FEATURES</h2>
  <div class="feature-grid">
    <div class="feature">
      <svg viewBox="0 0 44 44" fill="var(--ink)"><circle cx="22" cy="12" r="9"/><path d="M4 42c0-12 8-18 18-18s18 6 18 18z"/></svg>
      <p>Professional service on location. Don’t ship to us we will come to you!</p>
    </div>
    <div class="feature">
      <svg viewBox="0 0 44 44" fill="none" stroke="var(--ink)" stroke-width="3"><rect x="3" y="8" width="38" height="28" rx="2"/><line x1="3" y1="17" x2="41" y2="17" stroke-width="5"/><line x1="9" y1="29" x2="18" y2="29"/><line x1="22" y1="29" x2="28" y2="29"/></svg>
      <p>Clear pricing upfront. No hidden cost.</p>
    </div>
    <div class="feature">
      <svg viewBox="0 0 44 44" fill="none" stroke="var(--ink)" stroke-width="3.5"><circle cx="22" cy="22" r="18"/><path d="M22 11v12h-8"/></svg>
      <p>Next business-day repair.</p>
    </div>
    <div class="feature">
      <svg viewBox="0 0 44 44" fill="none" stroke="var(--ink)" stroke-width="3"><rect x="8" y="4" width="28" height="36" rx="3"/><rect x="12" y="9" width="20" height="24" fill="var(--ink)" stroke="none"/></svg>
      <p>Backed by a professional repair center with more then 12 years of experience</p>
    </div>
    <div class="feature">
      <svg viewBox="0 0 44 44"><path d="M6 5h32v16c0 10-8 16-16 20C14 37 6 31 6 21z" fill="var(--ink)"/><path d="M22 9h12v12c0 8-6 13-12 16z" fill="var(--white)"/></svg>
      <p>Repair is done by certified engineers</p>
    </div>
    <div class="feature">
      <svg viewBox="0 0 44 44" fill="none" stroke="var(--ink)" stroke-width="2.5"><rect x="4" y="8" width="36" height="32" rx="2"/><rect x="4" y="8" width="36" height="7" fill="var(--ink)"/><line x1="12" y1="3" x2="12" y2="11"/><line x1="32" y1="3" x2="32" y2="11"/><path d="M4 23h36M4 31h36M13 15v25M22 15v25M31 15v25" stroke-width="1.5"/></svg>
      <p>1 year warranty on the repair</p>
    </div>
  </div>
</section>

<section class="newsletter">
  <h3>GET TAX COUPONS &amp; THE LATEST DEALS</h3>
  <div class="field">Enter Your Email Id</div>
  <div class="btn-sign">SIGN UP</div>
</section>

<footer class="site-footer">
  <div class="footer-col" style="left:132px">
    <h4>Credit Cards ›</h4>
    <ul><li>Make Payment/Check Balance</li><li>Credit Card Offers</li><li>Apply Now</li></ul>
  </div>
  <div class="footer-col" style="left:384px">
    <h4>Orders &amp; Returns ›</h4>
    <ul><li>Order Status</li><li>Shipping, Delivery &amp; Store Pickup</li><li>Return &amp; Exchange Promise</li><li>Price Match Guarantee</li><li>Pay With Points</li><li>More Orders &amp; Returns Help</li></ul>
  </div>
  <div class="footer-col" style="left:672px">
    <h4>Support &amp; Services ›</h4>
    <ul><li>Customer Service</li><li>Protection Plans</li><li>Schedule a Service</li><li>Trade-In Program</li><li>Product Recalls</li><li>More Support &amp; Services</li></ul>
  </div>
  <div class="social" aria-label="Social media links"><i></i><i></i><i></i><i></i></div>
  <p class="copyright">©2017 Handset Haven. All Rights Reserved.</p>
</footer>

</body>
</html>
```